TalkHarbor - Language Coaching Services

Sleek, innovative, trendy design for Language Coaching business.

TalkHarbor is a new UK based company that provides Language Coaching services. We offer highly personalized on-line and face to face language courses. We also impart learning techniques workshops based on the latest neuroscience research for second-language acquisition.

Target Market(s)

See attached info

Industry/Entity Type

Consulting

Contact Information for Business Card

TalkHarbor
DaniaKV@talkharbor.co.uk
TalkHarbor.co.uk
London, UK

Font styles to use
Sans Serif

```html
<!DOCTYPE html>
<html lang="en">
<head>
<meta charset="utf-8">
<title>TalkHarbor – Business Card</title>
<link href="https://fonts.googleapis.com/css2?family=Montserrat:wght@500&family=Open+Sans:wght@400&display=swap" rel="stylesheet">
<style>
  :root {
    --backdrop: #e9e9e9;
    --card-front: #ffffff;
    --card-back: #231f20;
    --brand-blue: #1a8bc9;
    --band-blue: #0a86c2;
    --ink: #2b2b2b;
    --back-text: #d9d9d9;
    --band-text: #ffffff;
  }
  html, body {
    margin: 0;
    width: 1200px;
    height: 909px;
    overflow: hidden;
    background: var(--backdrop);
  }
  .card {
    position: absolute;
    left: 240px;
    width: 720px;
    height: 410px;
    box-shadow: 0 2px 10px rgba(0,0,0,0.10);
  }
  .card-back  { top: 28px;  background: var(--card-back); }
  .card-front { top: 470px; background: var(--card-front); }

  .brand {
    position: absolute;
    left: 0;
    width: 100%;
    text-align: center;
  }
  .brand-circle {
    display: block;
    margin: 0 auto;
    width: 110px;
    height: 110px;
  }
  .brand-name {
    margin: 14px 0 0;
    font-family: "Montserrat", sans-serif;
    font-weight: 500;
    font-size: 44px;
    letter-spacing: 2px;
    color: var(--brand-blue);
    line-height: 1;
  }
  .card-front .brand { top: 42px; }
  .card-back  .brand { top: 110px; }
  .back-web {
    margin: 16px 0 0;
    font-family: "Open Sans", sans-serif;
    font-size: 16px;
    letter-spacing: 0.5px;
    color: var(--back-text);
  }

  .contact-item {
    position: absolute;
    top: 247px;
    font-family: "Open Sans", sans-serif;
    font-size: 19px;
    color: var(--ink);
    white-space: nowrap;
  }
  .contact-item svg {
    display: block;
    width: 20px;
    height: 20px;
    margin: 0 0 12px 4px;
  }
  .contact-phone { left: 36px; }
  .contact-email { left: 216px; }
  .contact-web   { left: 482px; }
  .address-band {
    position: absolute;
    left: 0;
    top: 343px;
    width: 100%;
    height: 42px;
    background: var(--band-blue);
    color: var(--band-text);
    font-family: "Open Sans", sans-serif;
    font-size: 19px;
    line-height: 42px;
    text-align: center;
  }
</style>
</head>
<body>
  <section class="card card-back">
    <div class="brand">
      <p class="brand-name">TALKHARBOR</p>
      <p class="back-web">www.talkharbor.co.uk</p>
    </div>
  </section>

  <main class="card card-front">
    <div class="brand">
      <svg class="brand-circle" viewBox="0 0 110 110" aria-hidden="true">
        <circle cx="55" cy="55" r="50" fill="none" stroke="var(--brand-blue)" stroke-width="7"/>
      </svg>
      <p class="brand-name">TALKHARBOR</p>
    </div>

    <div class="contact-item contact-phone">
      <svg viewBox="0 0 24 24" aria-hidden="true">
        <path fill="var(--brand-blue)" d="M6.6 10.8a15.1 15.1 0 0 0 6.6 6.6l2.2-2.2c.3-.3.7-.4 1-.2 1.1.4 2.3.6 3.6.6.6 0 1 .4 1 1V20c0 .6-.4 1-1 1C10.6 21 3 13.4 3 4c0-.6.4-1 1-1h3.5c.6 0 1 .4 1 1 0 1.3.2 2.5.6 3.6.1.3 0 .7-.2 1z"/>
      </svg>
      +44 1632 960418
    </div>

    <div class="contact-item contact-email">
      <svg viewBox="0 0 24 24" aria-hidden="true">
        <rect x="2" y="5" width="20" height="14" fill="var(--brand-blue)"/>
        <path d="M2.5 5.5 12 13l9.5-7.5M2.5 18.5l7-6.5M21.5 18.5l-7-6.5" fill="none" stroke="#fff" stroke-width="1.4"/>
      </svg>
      daniakv@talkharbor.co.uk
    </div>

    <div class="contact-item contact-web">
      <svg viewBox="0 0 24 24" aria-hidden="true">
        <g fill="none" stroke="var(--brand-blue)" stroke-width="1.8">
          <circle cx="12" cy="12" r="9.5"/>
          <ellipse cx="12" cy="12" rx="4.2" ry="9.5"/>
          <path d="M2.5 12h19M4 7h16M4 17h16M12 2.5v19"/>
        </g>
      </svg>
      www.talkharbor.co.uk
    </div>

    <div class="address-band">27 Harbour Lane, TN34 2QX, London, UK</div>
  </main>
</body>
</html>
```